Brisk. Technology Logistics Software platform.

A modern looking and feeling website for a logistics software platform.
We connect retailers or wholesale parcel distributors to worldwide delivery solutions.
Methods tend to be road and air transport to final mile courier companies and post offices all over the world.
Our platform is for ecommerce distribution. A customer uses BRISK to enable them to connect to worldwide companies who will track and trace the delivery of their goods.

Target Market(s)

Onllne retailers. Markert Places such as Vendora and Tradelo. Wholesale third party logistics and packaging companies. Delivery companies based in the UK looking to expand overseas.

Number of Pages Required

5+ page

Font styles to use
Sans Serif

Colors
aaaaaa
dbdbdb
e6e6e6
c4c4c4
cbcbcb
c9c9c9
ec1f27
3176b5
0355a3

Requirements
Must have
• Landing Page.
• What we do.
• Who we are.
• Modules.
• Testimonies (password protected)
• Contact us.
• Interactive for mobile operating systems.
• Scrolling website.
• Short stock video showing on key pages.
• Very well polished fonts and buttons. A sharp and well executed website is required.
• Simplicity in feeling.
• To the point on message.
• Refined wording and copyrighting / messaging
• A link to our sub brand and product Brisk Parcels
• Capture interest so people read further.
Nice to have
• A polished video to explain what we do on landing page. Clipmarrow.net have some good options but not sure how professional they will look.
Should not have
• Bad graphics and colours.
• Not lots of clicks. Less as possible
• Complex message

```html
<!DOCTYPE html>
<html lang="en">
<head>
<meta charset="utf-8">
<title>Brisk. Technology – Website Concepts</title>
<link rel="stylesheet" href="https://fonts.googleapis.com/css2?family=Montserrat:wght@600;700;800&family=Open+Sans:wght@400;600;700&display=swap">
<style>
:root{
  --board:#c4c4c4;
  --red:#ec1f27;
  --blue:#0355a3;
  --blue-mid:#3176b5;
  --band:#aaaaaa;
  --footer-bg:#f3f1f1;
  --ink:#222;
  --body:#333;
  --white:#fff;
}
*{box-sizing:border-box;margin:0;padding:0}
html,body{width:1200px;height:860px;overflow:hidden}
body{background:var(--board);font-family:"Open Sans",sans-serif;color:var(--body);position:relative}
.panel{position:absolute;background:var(--white);box-shadow:0 2px 6px rgba(0,0,0,.25);overflow:hidden}
.abs{position:absolute}
.brand{font-family:"Montserrat",sans-serif;font-weight:800;color:var(--red);display:flex;align-items:center;gap:4px;white-space:nowrap}
.brand .dot{width:8px;height:8px;border-radius:50%;background:var(--red)}

/* landing concept */
.landing{left:18px;top:16px;width:572px;height:344px}
.landing .photo{inset:0;background:
  radial-gradient(ellipse 38% 22% at 45% 18%,rgba(214,110,40,.75),rgba(214,110,40,0) 100%),
  radial-gradient(ellipse 22% 28% at 20% 60%,rgba(40,110,190,.7),rgba(40,110,190,0) 100%),
  radial-gradient(ellipse 20% 25% at 88% 62%,rgba(50,120,200,.6),rgba(50,120,200,0) 100%),
  radial-gradient(ellipse 25% 35% at 12% 30%,rgba(190,190,195,.45),rgba(190,190,195,0) 100%),
  radial-gradient(ellipse 30% 18% at 75% 22%,rgba(180,40,40,.55),rgba(180,40,40,0) 100%),
  linear-gradient(180deg,#3a3234 0%,#5c5048 30%,#5a6068 58%,#9ea2a8 80%,#c9cacd 100%)}
.landing .brand{left:0;right:0;top:36px;justify-content:center;font-size:17px}
.landing .headline{left:0;right:0;top:115px;text-align:center;font-family:"Montserrat",sans-serif;font-weight:800;font-size:16.5px;color:var(--white);text-shadow:0 1px 3px rgba(0,0,0,.5)}
.focus-box{left:153px;top:137px;width:284px;height:144px;background:rgba(255,255,255,.88);padding:15px 12px 0 17px}
.focus-item{display:flex;align-items:center;gap:10px;margin-bottom:14px;font-size:7.6px;line-height:1.35;color:var(--ink)}
.focus-item svg{flex:none}
.landing .copy{left:0;right:0;top:315px;text-align:center;font-size:6px;color:var(--white)}

/* home concept */
.home{left:611px;top:16px;width:573px;height:818px}
.hero{left:0;top:0;width:573px;height:324px;background:
  radial-gradient(ellipse 14% 12% at 42% 85%,rgba(230,170,30,.85),rgba(230,170,30,0) 100%),
  radial-gradient(ellipse 30% 25% at 78% 60%,rgba(205,190,150,.8),rgba(205,190,150,0) 100%),
  radial-gradient(ellipse 22% 30% at 20% 65%,rgba(225,220,210,.75),rgba(225,220,210,0) 100%),
  radial-gradient(ellipse 18% 45% at 52% 30%,rgba(170,185,200,.55),rgba(170,185,200,0) 100%),
  radial-gradient(ellipse 25% 18% at 95% 95%,rgba(200,120,40,.6),rgba(200,120,40,0) 100%),
  linear-gradient(180deg,#4a4c52 0%,#7d7566 35%,#a2957c 60%,#6f604c 88%,#3d342a 100%)}
.hero-shade{left:0;top:0;width:573px;height:324px;background:linear-gradient(180deg,rgba(0,0,0,.25),rgba(0,0,0,0) 40%)}
.home .top-brand{left:67px;top:14px;font-size:16px}
.nav{right:12px;top:14px;display:flex;gap:10px;align-items:center;font-family:"Montserrat",sans-serif;font-weight:700;font-size:7px;color:var(--white)}
.nav .active{background:var(--red);padding:4px 6px}
.hero-title{left:0;right:0;top:137px;text-align:center;font-family:"Montserrat",sans-serif;font-weight:800;font-size:13px;line-height:1.12;color:var(--white);text-shadow:0 1px 3px rgba(0,0,0,.7)}
.welcome-photo{left:67px;top:349px;width:212px;height:187px;background:
  radial-gradient(ellipse 22% 40% at 88% 72%,rgba(225,210,60,.75),rgba(225,210,60,0) 100%),
  radial-gradient(ellipse 30% 22% at 52% 62%,rgba(210,225,235,.75),rgba(210,225,235,0) 100%),
  radial-gradient(ellipse 40% 35% at 30% 25%,rgba(120,190,230,.7),rgba(120,190,230,0) 100%),
  radial-gradient(ellipse 15% 20% at 75% 28%,rgba(90,150,190,.7),rgba(90,150,190,0) 100%),
  linear-gradient(135deg,#1a3f66 0%,#0f2a48 50%,#081628 100%)}
.welcome{left:305px;top:368px;width:205px}
.welcome .kicker{font-family:"Montserrat",sans-serif;font-weight:700;font-size:11px;color:var(--ink)}
.welcome .title{font-family:"Montserrat",sans-serif;font-weight:800;font-size:17.5px;color:var(--red);margin-top:2px}
.welcome .rule{width:28px;height:2px;background:#999;margin:5px 0 18px}
.welcome p{font-size:7.6px;line-height:1.35;color:var(--body);margin-bottom:14px}
.band{left:0;top:560px;width:573px;height:96px;background:var(--band);text-align:center;color:var(--white);font-weight:700;font-size:11.5px;padding-top:25px;line-height:1.4}
.band .row{display:flex;justify-content:center;align-items:center;gap:4px}
.btn{font-family:"Montserrat",sans-serif;font-size:7.5px;padding:5px 7px;color:var(--white)}
.btn-blue{background:var(--blue-mid)}
.btn-red{background:var(--red)}
.footer{left:0;top:656px;width:573px;height:162px;background:var(--footer-bg)}
.footer .brand{left:69px;top:46px;font-size:28px}
.fcol{top:30px;font-size:5.5px;color:var(--ink);line-height:1.6}
.fcol h4{font-family:"Montserrat",sans-serif;font-size:6px;font-weight:800;margin-bottom:7px}
.fline{display:flex;gap:5px;align-items:flex-start;margin-bottom:7px}
.social{display:flex;align-items:center;gap:6px;margin-bottom:7px}
.social i{width:12px;height:12px;border-radius:50%;display:block}
.footer .rule{left:55px;top:122px;width:450px;height:1px;background:#ccc}
.footer .copy{left:0;right:0;top:139px;text-align:center;font-size:5.5px;color:var(--ink)}
</style>
</head>
<body>

<section class="panel landing">
  <div class="abs photo" role="img" aria-label="Industrial warehouse interior with overlaid technical wireframe lines"></div>
  <div class="abs brand"><span>Brisk. Technology</span><span class="dot"></span></div>
  <h1 class="abs headline">BRISK.TECHNOLOGY ... OUR FOCUS</h1>
  <div class="abs focus-box">
    <div class="focus-item">
      <svg width="28" height="28" viewBox="0 0 28 28"><circle cx="14" cy="14" r="14" fill="#ec1f27"/><g stroke="#fff" stroke-width="1.6" stroke-linecap="round"><line x1="8" y1="10" x2="20" y2="10"/><line x1="8" y1="14" x2="20" y2="14"/><line x1="8" y1="18" x2="20" y2="18"/></g></svg>
      <span>We provide advanced software solutions to ensure you connect with global e commerce delivery carriers</span>
    </div>
    <div class="focus-item">
      <svg width="28" height="28" viewBox="0 0 28 28"><circle cx="14" cy="14" r="14" fill="#ec1f27"/><g fill="none" stroke="#fff" stroke-width="1.3"><circle cx="14" cy="14" r="7"/><ellipse cx="14" cy="14" rx="3" ry="7"/><line x1="7" y1="14" x2="21" y2="14"/></g></svg>
      <span>You can manage your Global Delivery Network in one place, with our software will enable you monitor the productivity and reporting of your e commerce deliveries</span>
    </div>
    <div class="focus-item">
      <svg width="28" height="28" viewBox="0 0 28 28"><circle cx="14" cy="14" r="14" fill="#ec1f27"/><circle cx="14" cy="14" r="6" fill="none" stroke="#fff" stroke-width="3" stroke-dasharray="3 1.7"/><circle cx="14" cy="14" r="2" fill="#fff"/></svg>
      <span>Manage your carriers, your delivery speeds,<br>and your costs</span>
    </div>
  </div>
  <p class="abs copy">Copyrights @ 2018 All Rights Reserved</p>
</section>

<section class="panel home">
  <div class="abs hero" role="img" aria-label="Warehouse aisle with stacked boxes on shelving and a forklift"></div>
  <div class="abs hero-shade"></div>
  <div class="abs brand top-brand"><span>Brisk. Technology</span><span class="dot"></span></div>
  <nav class="abs nav"><span class="active">HOME</span><span>SOLUTIONS</span><span>TESTIMONIAL LOGIN</span><span>CONTACT US</span></nav>
  <h1 class="abs hero-title">BRISK. TECHNOLOGY AND PARCEL SOLUTIONS<br>BUILT TO HELP DEVELOP &amp; MANAGE YOUR<br>GLOBAL DELIVERY NETWORK</h1>

  <div class="abs welcome-photo" role="img" aria-label="Engineer in hard hat holding a laptop among glowing data graphics"></div>
  <div class="abs welcome">
    <p class="kicker">WELCOME TO</p>
    <h2 class="title">BRISK TECHNOLOGY.</h2>
    <div class="rule"></div>
    <p>Working closely with Ecommerce, Brisk. Technology have developed solutions purely focused on delivering what's required within the global delivery marketplace. Meeting all needs and more for Retailers and Global Delivery Solution providers</p>
    <p>Allowing customers to grow at a fast pace; most importantly providing tools to help them manage their global delivery network supported by “Dynamic Real Time Visibility” management tools</p>
  </div>

  <div class="abs band">
    <div class="row"><span>Ensuring&nbsp;</span><span class="btn btn-blue">BRISK PARCELS</span><span class="btn btn-red">BRISK TECHNOLOGY</span></div>
    <div>solutions evolve to suit our customers<br>business requirements</div>
  </div>

  <footer class="abs footer">
    <div class="abs brand"><span>Brisk.</span><span class="dot"></span></div>
    <div class="abs fcol" style="left:238px">
      <h4>CONTACT US</h4>
      <div class="fline"><svg width="5" height="7" viewBox="0 0 10 14"><path d="M5 0a5 5 0 0 1 5 5c0 4-5 9-5 9S0 9 0 5a5 5 0 0 1 5-5z" fill="#222"/><circle cx="5" cy="5" r="2" fill="#fff"/></svg><span>58 Harbour Row<br>Millbrook, IL 60999</span></div>
      <div class="fline"><svg width="6" height="6" viewBox="0 0 12 12"><path d="M2 0l3 3-1.5 1.5a8 8 0 0 0 4 4L9 7l3 3-2 2C5 12 0 7 0 2z" fill="#222"/></svg><span>555.010.2040</span></div>
      <div class="fline"><svg width="7" height="5" viewBox="0 0 14 10"><rect width="14" height="10" fill="#222"/><path d="M0 0l7 6 7-6" fill="none" stroke="#fff" stroke-width="1.2"/></svg><span>hello@brisktech.example</span></div>
    </div>
    <div class="abs fcol" style="left:350px">
      <h4>MENU</h4>
      <div>Home<br>Solutions<br>Testimonial Login<br>Contact Us</div>
    </div>
    <div class="abs fcol" style="left:440px">
      <h4>CONNECT WITH US</h4>
      <div class="social"><i style="background:var(--blue)"></i><span>Chatter</span></div>
      <div class="social"><i style="background:var(--blue-mid)"></i><span>Flutter</span></div>
      <div class="social"><i style="background:#1b2a4a"></i><span>Workly</span></div>
    </div>
    <div class="abs rule"></div>
    <p class="abs copy">Copyrights @ 2018 All Rights Reserved</p>
  </footer>
</section>

</body>
</html>
```